Business Card Design

I need a logo and a business card design that can be used for my business stationary, Facebook page and in the future a website. I don't know if I need a large design for brochures and stationery and a small portion of that as the logo or business card design. I probably need some advice about that. My new company is called Willowbank Family Circle. I don't have all of my business contact details available yet, but I want to get the design ready, so that when all this information is available I can get the printing done quickly.I'm a social worker and my business will be providing parenting groups and counselling sessions for parents.I would like the logo and business card to be very feminine and pretty. I want a silhouette image of a Mother and Baby and decorative swirls of flowers/vines/leaves and butterflies.I have found some designs elsewhere that are along the lines of what I am looking for. These images are attached below, but the quality of these attachments is very poor as I photographed them with my phone.My preferred colours would be to use black and white, purple and/or pink, aqua and or blue/green.There are four logo/business card options attached. Logo option 1 - I really like the flower and vine design. Logo option 2 - again I like the flowers and leaf design and the use of colour and the silhouette image of the Mum and Baby; Logo option 3 - I like the butterflies and decorative swirls in this option and Logo option 4 - I think this design is the best for a logo. I love the mother and baby image. I don't like the tree branch and the birds but I like the way the hair has been incorporated into the branch. I prefer the design of the flowers/vine/leaves in the other options.

Industry/Entity Type

Business

Contact Information for Business Card

Company Name:Embrace Attachment ParentingMobile:0417 751 394Email:Currently sourcing - TBAContact Name:Janelle ApplegarthQualifications:Currently sourcing details - TBA

Font styles to use
Script

Colors
33a6d7
85cae6
886aae
6c459b
e667a6
eea4c8

Requirements
Must have
• My project must have an image of a mother and child, slightly encircled by the mother's hair perhaps in a heart shape, and the mother's hair becoming a beautiful filigree design of vine/leaves/flowers and with some butterfly somewhere.
• Can all of the Words be in the same font Attachment Parenting can be slightly smaller.
Nice to have
• I would like to also have a similar vine/leaves/flowers and maybe a butterfly on the opposite side of the card. Maybe the Mother/child image on the top left of the card and the other pattern on the bottom right.
• If possible the use of aqua, purple and pink.

```html
<!DOCTYPE html>
<html lang="en">
<head>
<meta charset="utf-8">
<title>Willowbank Family Circle – Business Card</title>
<link rel="stylesheet" href="https://fonts.googleapis.com/css2?family=Arimo:wght@400;700&family=Pinyon+Script&display=swap">
<style>
  :root {
    --backdrop: #ece7e2;
    --card: #ffffff;
    --pink-strong: #ea3f94;
    --pink-text: #e0479a;
    --pink-soft: #e9a3c7;
    --pink-faint: #fbe9f2;
    --pink-mist: #fdf3f8;
    --band: #ec4196;
    --band-line: #e8a0c8;
  }
  * { margin: 0; padding: 0; box-sizing: border-box; }
  html, body {
    width: 902px;
    height: 1200px;
    overflow: hidden;
    background: var(--backdrop);
    font-family: "Arimo", Arial, sans-serif;
  }
  .business-card {
    position: absolute;
    left: 151px;
    top: 76px;
    width: 600px;
    height: 1048px;
    background: var(--card);
    border-radius: 18px;
    overflow: hidden;
    box-shadow: 0 6px 24px rgba(90, 60, 70, 0.18);
  }
  .background-flourish {
    position: absolute;
    left: 0;
    top: 260px;
    width: 600px;
    height: 660px;
  }
  .emblem-area {
    position: absolute;
    left: 95px;
    top: 81px;
    width: 373px;
    height: 335px;
  }
  .brand-mark {
    position: absolute;
    left: 190px;
    top: 154px;
    width: 208px;
    height: 208px;
    border-radius: 50%;
    background: var(--pink-strong);
    box-shadow: 0 0 0 8px var(--card), 0 0 0 12px var(--pink-soft);
  }
  .brand-name {
    position: absolute;
    left: 0;
    right: 0;
    top: 412px;
    text-align: center;
    font-family: "Pinyon Script", cursive;
    font-weight: 400;
    color: var(--pink-text);
  }
  .brand-name-primary {
    display: block;
    font-size: 84px;
    line-height: 100px;
  }
  .brand-name-secondary {
    display: block;
    font-size: 46px;
    line-height: 52px;
  }
  .contact-person {
    position: absolute;
    left: 0;
    right: 0;
    top: 650px;
    text-align: center;
  }
  .person-name {
    font-size: 33px;
    font-weight: 700;
    color: var(--pink-text);
    line-height: 38px;
  }
  .person-qualifications {
    font-size: 30px;
    color: var(--pink-soft);
    line-height: 34px;
  }
  .contact-details {
    position: absolute;
    left: 0;
    right: 0;
    top: 818px;
    text-align: center;
    font-size: 30px;
    line-height: 35px;
    color: var(--pink-text);
  }
  .contact-label {
    font-weight: 700;
    color: var(--pink-soft);
  }
  .footer-rule {
    position: absolute;
    left: 0;
    top: 953px;
    width: 600px;
    height: 6px;
    background: var(--band-line);
  }
  .footer-band {
    position: absolute;
    left: 0;
    top: 966px;
    width: 600px;
    height: 82px;
    background: var(--band);
  }
</style>
</head>
<body>
  <article class="business-card">
    <svg class="background-flourish" viewBox="0 0 600 660" role="img" aria-label="Faint pink swirling vine and flower pattern in the card background">
      <defs>
        <radialGradient id="flourishTone" cx="40%" cy="55%" r="65%">
          <stop offset="0%" stop-color="var(--pink-faint)"/>
          <stop offset="100%" stop-color="var(--pink-mist)" stop-opacity="0"/>
        </radialGradient>
      </defs>
      <rect width="600" height="660" fill="url(#flourishTone)"/>
    </svg>

    <svg class="emblem-area" viewBox="0 0 373 335" role="img" aria-label="Pink flowers, curling vines and leaves surrounding the brand mark">
      <defs>
        <radialGradient id="floralTone" cx="50%" cy="50%" r="55%">
          <stop offset="0%" stop-color="#f4c6dd"/>
          <stop offset="100%" stop-color="#f4c6dd" stop-opacity="0"/>
        </radialGradient>
      </defs>
      <rect width="373" height="335" fill="url(#floralTone)"/>
    </svg>

    <div class="brand-mark" aria-hidden="true"></div>

    <h1 class="brand-name">
      <span class="brand-name-primary">Willowbank</span>
      <span class="brand-name-secondary">Family Circle</span>
    </h1>

    <section class="contact-person">
      <p class="person-name">Rosalind Thackeray</p>
      <p class="person-qualifications">Currently sourcing details - TBA</p>
    </section>

    <section class="contact-details">
      <p><span class="contact-label">M:</span> 0438 260 517</p>
      <p><span class="contact-label">E:</span> Currently sourcing - TBA</p>
    </section>

    <div class="footer-rule"></div>
    <div class="footer-band"></div>
  </article>
</body>
</html>
```